Business Card Design

New business card design

Target Market(s)

Residential & Commercial Property Managers

Industry/Entity Type

Plumbing Services

Contact Information for Business Card

Name - Rowan Keddle, title - Director, Phone Number - 0431 286 517, email - rowan@tbk-plumbing.com.au, Company ABN - 73 215 904 386,

Font styles to use
Sans Serif

Colors
0054AA
0677BA
7BADD7
CADEEF
E8F1F8

```html
<!DOCTYPE html>
<html lang="en">
<head>
<meta charset="utf-8">
<title>TBK Plumbing Services – Business Card</title>
<link rel="stylesheet" href="https://fonts.googleapis.com/css2?family=Questrial&family=Roboto:wght@300;400;700&display=swap">
<style>
  :root {
    --backdrop: #2a2a2a;
    --card-white: #f7f7f7;
    --card-taupe: #6b6259;
    --ink: #1a1a1a;
    --ink-soft: #8a8a8a;
    --band-black: #0b0b0b;
    --accent-blue: #1a9ddc;
    --band-taupe: #766c62;
    --on-dark: #ffffff;
  }
  * { margin: 0; padding: 0; box-sizing: border-box; }
  html, body { width: 1200px; height: 852px; overflow: hidden; }
  body {
    background: var(--backdrop);
    position: relative;
    font-family: "Roboto", Arial, sans-serif;
  }
  .card {
    position: absolute;
    top: 271px;
    width: 540px;
    height: 310px;
    border-radius: 20px;
    overflow: hidden;
  }
  .card--back { left: 40px; background: var(--card-taupe); }
  .card--front { left: 620px; background: var(--card-white); }

  .brand {
    position: absolute;
    font-family: "Questrial", Arial, sans-serif;
    color: var(--ink);
    display: flex;
    align-items: center;
    gap: 10px;
    white-space: nowrap;
  }
  .brand__dot {
    width: 12px; height: 12px; border-radius: 50%;
    background: var(--accent-blue);
  }
  .brand__name { font-size: 34px; letter-spacing: 1px; }
  .card--back .brand { left: 0; right: 0; top: 130px; justify-content: center; }
  .card--front .brand { left: 30px; top: 140px; }
  .card--front .brand__name { font-size: 22px; letter-spacing: 0.5px; }

  .card__waves { position: absolute; inset: 0; width: 540px; height: 310px; }

  .holder { position: absolute; right: 36px; top: 40px; text-align: right; }
  .holder__name { font-weight: 700; font-size: 19px; color: var(--ink); }
  .holder__title { font-weight: 300; font-size: 13px; color: var(--ink-soft); margin-top: 2px; }

  .contacts {
    position: absolute; right: 18px; top: 168px;
    list-style: none; text-align: right;
    color: var(--on-dark); font-weight: 300; font-size: 12px;
  }
  .contacts li { display: flex; justify-content: flex-end; align-items: center; gap: 8px; height: 19px; }
  .contacts .icon { width: 11px; height: 11px; fill: var(--accent-blue); }
  .contacts .icon-gap { width: 11px; }
</style>
</head>
<body>

  <section class="card card--back" aria-label="Business card back">
    <div class="brand">
      <span class="brand__name">tbk plumbing services</span>
      <span class="brand__dot"></span>
    </div>
  </section>

  <section class="card card--front" aria-label="Business card front">
    <svg class="card__waves" viewBox="0 0 540 310" aria-hidden="true">
      <path d="M0,282 C160,286 260,266 322,205 C290,262 190,296 0,300 Z" fill="var(--band-taupe)"/>
      <path d="M540,92 C420,96 350,120 318,180 C285,245 210,285 0,292 L0,310 L540,310 Z" fill="var(--band-black)"/>
      <path d="M540,78 C412,82 338,108 304,172 C270,238 195,280 60,290" fill="none" stroke="var(--accent-blue)" stroke-width="4"/>
    </svg>

    <div class="brand">
      <span class="brand__name">tbk plumbing services</span>
      <span class="brand__dot"></span>
    </div>

    <div class="holder">
      <p class="holder__name">Rowan Keddle</p>
      <p class="holder__title">Director</p>
    </div>

    <ul class="contacts">
      <li>0431 286 517
        <svg class="icon" viewBox="0 0 24 24"><path d="M6.6 10.8a15 15 0 0 0 6.6 6.6l2.2-2.2c.3-.3.7-.4 1-.2 1.1.4 2.3.6 3.6.6.6 0 1 .4 1 1V20c0 .6-.4 1-1 1A17 17 0 0 1 3 4c0-.6.4-1 1-1h3.5c.6 0 1 .4 1 1 0 1.3.2 2.5.6 3.6.1.3 0 .7-.2 1z"/></svg>
      </li>
      <li>rowan@tbk-plumbing.com.au
        <svg class="icon" viewBox="0 0 24 24"><path d="M2 5h20v14H2z M2 5l10 8 10-8" fill="var(--accent-blue)" stroke="var(--band-black)" stroke-width="1.5"/></svg>
      </li>
      <li>www.tbk-plumbing.com.au
        <svg class="icon" viewBox="0 0 24 24"><circle cx="12" cy="12" r="10"/><path d="M2 12h20M12 2c3 3 3 17 0 20M12 2c-3 3-3 17 0 20" fill="none" stroke="var(--band-black)" stroke-width="1.5"/></svg>
      </li>
      <li>ABN 73 215 904 386 <span class="icon-gap"></span></li>
    </ul>
  </section>

</body>
</html>
```